Business Card Design Project

New business card design front and back for IT company that does network support and web design.
Calloway IT
Darren Calloway
Managing Director
PO Box 592 Fernleigh VIC 3471
darren@callowayit-example.com
www.callowayit-example.com

Industry/Entity Type

Business

```html
<!DOCTYPE html>
<html lang="en">
<head>
<meta charset="utf-8">
<title>Calloway IT – Business Card</title>
<link href="https://fonts.googleapis.com/css2?family=Lato:wght@400;700&display=swap" rel="stylesheet">
<style>
  :root {
    --brand-blue: #2aa8d8;
    --brand-blue-deep: #1f93c2;
    --brand-blue-light: #45b9e4;
    --ink: #2b2b2b;
    --ink-soft: #3a3a3a;
    --card-white: #f4f4f4;
    --backdrop: #e4e6e8;
  }
  * { box-sizing: border-box; margin: 0; padding: 0; }
  html, body {
    width: 1200px; height: 900px; overflow: hidden;
    background: var(--backdrop);
    font-family: "Lato", sans-serif;
  }
  .canvas {
    position: relative; width: 1200px; height: 900px;
    display: flex; flex-direction: column; align-items: center; justify-content: center; gap: 40px;
  }
  .card {
    position: relative; width: 700px; height: 400px; overflow: hidden;
    box-shadow: 0 6px 18px rgba(0,0,0,0.18);
  }

  /* Front */
  .card--front { background: var(--brand-blue); }
  .card--front .edge-stripe {
    position: absolute; left: 0; right: 0; bottom: 52px; height: 8px;
    background: var(--brand-blue-light);
  }
  .front-lockup {
    position: absolute; left: 70px; top: 120px;
    display: flex; align-items: center; gap: 34px;
  }
  .front-name {
    display: flex; align-items: center; gap: 14px;
    color: #ffffff; font-weight: 700; font-size: 40px; letter-spacing: 0.5px;
  }
  .front-name .mark-square { width: 26px; height: 26px; background: #ffffff; }
  .front-tagline { display: flex; flex-direction: column; }
  .front-tagline .tag-main { color: #eef8fc; font-weight: 700; font-size: 44px; line-height: 1.05; }
  .front-tagline .tag-sub { color: var(--ink); font-weight: 700; font-size: 22px; letter-spacing: 1.5px; }

  /* Back */
  .card--back { background: var(--card-white); }
  .brand-wordmark {
    position: absolute; left: 52px; top: 58px;
    color: var(--brand-blue); font-weight: 700; font-size: 44px; letter-spacing: 1px;
  }
  .person {
    position: absolute; left: 52px; top: 148px;
    display: flex; align-items: baseline; gap: 8px; color: var(--ink);
  }
  .person .person-name { font-weight: 700; font-size: 26px; }
  .person .divider { font-size: 22px; }
  .person .person-role { font-size: 17px; letter-spacing: 0.5px; text-transform: uppercase; }
  .contact-list {
    position: absolute; list-style: none;
    display: flex; flex-direction: column; gap: 12px;
    color: var(--ink-soft); font-size: 17px;
  }
  .contact-list--left { left: 52px; top: 216px; }
  .contact-list--right { left: 382px; top: 256px; }
  .contact-list li { display: flex; align-items: center; gap: 12px; }
  .contact-icon { width: 24px; height: 24px; flex: none; }
  .band {
    position: absolute; left: 0; right: 0; bottom: 0; height: 56px;
    background: var(--brand-blue);
  }
  .band::before {
    content: ""; position: absolute; left: 0; right: 0; top: 0; height: 10px;
    background: var(--brand-blue-deep);
  }
</style>
</head>
<body>
<main class="canvas">

  <section class="card card--front" aria-label="Business card front">
    <div class="front-lockup">
      <div class="front-name"><span class="mark-square"></span>Calloway IT</div>
      <div class="front-tagline">
        <span class="tag-main">IT Solutions</span>
        <span class="tag-sub">FOR YOUR BUSINESS</span>
      </div>
    </div>
    <div class="edge-stripe"></div>
  </section>

  <section class="card card--back" aria-label="Business card back">
    <div class="brand-wordmark">CALLOWAY IT</div>

    <div class="person">
      <span class="person-name">Darren Calloway</span>
      <span class="divider">|</span>
      <span class="person-role">Managing Director</span>
    </div>

    <ul class="contact-list contact-list--left">
      <li>
        <svg class="contact-icon" viewBox="0 0 24 24" aria-hidden="true">
          <circle cx="12" cy="12" r="12" fill="var(--brand-blue)"/>
          <path d="M8.5 6.5l2 2.2-1.2 1.4c.8 1.8 2 3 3.7 3.8l1.4-1.2 2.2 2-1.3 1.8c-4.2-.5-7.6-3.9-8.2-8.1z" fill="#fff"/>
        </svg>
        <span>0400 555 018</span>
      </li>
      <li>
        <svg class="contact-icon" viewBox="0 0 24 24" aria-hidden="true">
          <circle cx="12" cy="12" r="12" fill="var(--brand-blue)"/>
          <rect x="6" y="8" width="12" height="8.5" rx="1" fill="#fff"/>
          <path d="M6.5 8.6L12 13l5.5-4.4" fill="none" stroke="var(--brand-blue)" stroke-width="1.3"/>
        </svg>
        <span>darren@callowayit-example.com</span>
      </li>
    </ul>

    <ul class="contact-list contact-list--right">
      <li>
        <svg class="contact-icon" viewBox="0 0 24 24" aria-hidden="true">
          <circle cx="12" cy="12" r="12" fill="var(--brand-blue)"/>
          <path d="M12 5.5a4.2 4.2 0 0 0-4.2 4.2c0 3.1 4.2 8 4.2 8s4.2-4.9 4.2-8A4.2 4.2 0 0 0 12 5.5z" fill="#fff"/>
          <circle cx="12" cy="9.7" r="1.6" fill="var(--brand-blue)"/>
        </svg>
        <span>PO Box 592 Fernleigh VIC 3471</span>
      </li>
      <li>
        <svg class="contact-icon" viewBox="0 0 24 24" aria-hidden="true">
          <circle cx="12" cy="12" r="12" fill="var(--brand-blue)"/>
          <rect x="8.2" y="5.5" width="7.6" height="12.5" rx="3.8" fill="none" stroke="#fff" stroke-width="1.5"/>
          <line x1="12" y1="6" x2="12" y2="10" stroke="#fff" stroke-width="1.5"/>
        </svg>
        <span>www.callowayit-example.com</span>
      </li>
    </ul>

    <div class="band"></div>
  </section>

</main>
</body>
</html>
```